Oil Field Service company needs professional business cards

Looking to clean up our current company business cards and look a little more professional. Brenwick Casing Services is a US based company that services the oil field. We deal with engineers, managers and oil rigs....................................................................................................................................................................................................................................................................................................................................................................................................

Target Market(s)

Oil and Gas professionals

Industry/Entity Type

Oil And Gas

Contact Information for Business Card

See attached photo as example

Font styles to use
Sans Serif

Colors
ec1f27

Requirements
Must have
• Company Logo, Name, Title, Cell, Office, Fax, Email.
• See attached photo
Nice to have
• External CRT, Internal CRT, Casing Crews, Torque Turn, Laydown Machine
Should not have
• Do not introduce any new pictures and keep it professional looking

```html
<!DOCTYPE html>
<html lang="en">
<head>
<meta charset="utf-8">
<title>Brenwick Casing Services – Business Card</title>
<link rel="stylesheet" href="https://fonts.googleapis.com/css2?family=Oswald:wght@500&family=Roboto:wght@400;500;700&display=swap">
<style>
  :root {
    --slate: #3b5060;
    --red: #ec1f27;
    --red-deep: #d21c24;
    --paper: #f7f7f7;
    --ink: #333a40;
    --bg: #e4e4e4;
  }
  * { margin: 0; padding: 0; box-sizing: border-box; }
  html, body { width: 1200px; height: 576px; overflow: hidden; }
  body {
    background: var(--bg);
    position: relative;
    font-family: "Roboto", Arial, sans-serif;
  }
  .card {
    position: absolute;
    background: var(--paper);
    border-radius: 6px;
    overflow: hidden;
  }
  /* Front */
  .card-front { left: 82px; top: 139px; width: 484px; height: 293px; }
  .brand-front {
    position: absolute; left: 0; right: 0; top: 72px;
    text-align: center; color: var(--slate);
  }
  .brand-front .brand-name {
    font-weight: 700; font-size: 44px; letter-spacing: 1px;
    line-height: 1; text-transform: uppercase;
  }
  .brand-front .brand-sub {
    margin-top: 12px;
    font-weight: 700; font-size: 17px; letter-spacing: 3px;
    text-transform: uppercase;
  }
  .services-band {
    position: absolute; left: 0; right: 0; top: 220px; height: 26px;
    background: var(--red);
    display: flex; align-items: center; justify-content: center; gap: 8px;
    color: #fff; font-weight: 500; font-size: 12.5px; letter-spacing: 0.3px;
  }
  .services-band .divider { opacity: 0.9; }
  .front-web {
    position: absolute; left: 0; right: 0; top: 262px;
    display: flex; align-items: center; justify-content: center; gap: 10px;
    color: var(--ink); font-size: 13px;
  }
  .front-web .rule { width: 80px; height: 2px; background: var(--red); border-radius: 1px; }

  /* Back */
  .card-back { left: 602px; top: 138px; width: 481px; height: 291px; }
  .side-panel { position: absolute; left: 0; top: 0; }
  .brand-vertical {
    position: absolute; left: 94px; top: 145px;
    transform: translate(-50%, -50%) rotate(-90deg);
    white-space: nowrap; text-align: center; color: #fff;
  }
  .brand-vertical .brand-name {
    font-weight: 700; font-size: 30px; letter-spacing: 1px;
    text-transform: uppercase; line-height: 1;
  }
  .brand-vertical .brand-sub {
    margin-top: 8px; font-weight: 700; font-size: 11px; letter-spacing: 2.5px;
    text-transform: uppercase;
  }
  .holder {
    position: absolute; right: 27px; top: 22px; text-align: right; color: var(--ink);
  }
  .holder .holder-name { font-family: "Oswald", Arial, sans-serif; font-weight: 500; font-size: 22px; line-height: 1.1; }
  .holder .holder-title { font-size: 11px; margin-top: 2px; }
  .contact-list {
    position: absolute; right: 27px; top: 174px; list-style: none; color: var(--ink);
    font-size: 11.5px;
  }
  .contact-list li {
    display: flex; justify-content: flex-end; align-items: center; gap: 8px;
    height: 16.2px;
  }
  .contact-list svg { width: 10px; height: 10px; fill: var(--red); flex: none; }
</style>
</head>
<body>

<section class="card card-front">
  <div class="brand-front">
    <div class="brand-name">Brenwick</div>
    <div class="brand-sub">Casing Services</div>
  </div>
  <div class="services-band">
    <span>LAYDOWN MACHINE</span><span class="divider">|</span>
    <span>CASING CREW</span><span class="divider">|</span>
    <span>MUD TOOL</span><span class="divider">|</span>
    <span>TORQUE TURN</span>
  </div>
  <div class="front-web">
    <span class="rule"></span><span>www.brenwickcs.com</span><span class="rule"></span>
  </div>
</section>

<section class="card card-back">
  <svg class="side-panel" width="220" height="291" viewBox="0 0 220 291">
    <path d="M0 0 H184 C208 70 222 140 212 200 C204 248 190 275 178 291 H0 Z" fill="var(--red)"/>
    <path d="M0 0 H180 C202 70 214 140 203 200 C195 248 176 276 164 291 H0 Z" fill="var(--slate)"/>
  </svg>
  <div class="brand-vertical">
    <div class="brand-name">Brenwick</div>
    <div class="brand-sub">Casing Services</div>
  </div>

  <div class="holder">
    <div class="holder-name">Cole Harlan</div>
    <div class="holder-title">Area Manager</div>
  </div>

  <ul class="contact-list">
    <li><span>(555) 310-4820</span>
      <svg viewBox="0 0 10 10"><path d="M2 0.5 L3.6 2.6 L2.8 3.6 C3.4 5 4.8 6.4 6.3 7.1 L7.3 6.3 L9.5 7.9 L8.4 9.5 C4.5 9 1 5.6 0.5 1.6 Z"/></svg></li>
    <li><span>(555) 310-6157</span>
      <svg viewBox="0 0 10 10"><path d="M0.5 3 C2 1 8 1 9.5 3 L8.5 4.2 L7 3.6 L7 2.8 C6 2.4 4 2.4 3 2.8 L3 3.6 L1.5 4.2 Z M2.5 5 H7.5 L8.5 9 H1.5 Z"/></svg></li>
    <li><span>(555) 310-4833</span>
      <svg viewBox="0 0 10 10"><path d="M2.5 0.5 H7.5 V3 H2.5 Z M0.5 3.5 H9.5 V7.5 H8 V6 H2 V7.5 H0.5 Z M2.5 6.5 H7.5 V9.5 H2.5 Z"/></svg></li>
    <li><span>Ashby, OK 73990</span>
      <svg viewBox="0 0 10 10"><path d="M5 0.3 C2.9 0.3 1.5 1.9 1.5 3.8 C1.5 6.2 5 9.7 5 9.7 C5 9.7 8.5 6.2 8.5 3.8 C8.5 1.9 7.1 0.3 5 0.3 Z M5 2.4 A1.4 1.4 0 1 1 5 5.2 A1.4 1.4 0 1 1 5 2.4 Z" fill-rule="evenodd"/></svg></li>
    <li><span>coleharlan@brenwickcs.com</span>
      <svg viewBox="0 0 10 10"><path d="M0.5 2 H9.5 V8 H0.5 Z M1.2 2.6 L5 5.6 L8.8 2.6" stroke="#fff" stroke-width="0.8"/></svg></li>
    <li><span>www.brenwickcs.com</span>
      <svg viewBox="0 0 10 10"><circle cx="5" cy="5" r="4.5"/><path d="M0.5 5 H9.5 M5 0.5 C3 3 3 7 5 9.5 M5 0.5 C7 3 7 7 5 9.5 M1.3 2.8 H8.7 M1.3 7.2 H8.7" stroke="#fff" stroke-width="0.6" fill="none"/></svg></li>
  </ul>
</section>

</body>
</html>
```